Education Certificate

We need a modern yet professional Certificate for those who successfully pass / complete our online Training course.

There are various courses but ONE certificate design required.

the certificate needs to look extremely professional and of value.

```html
<!DOCTYPE html>
<html lang="en">
<head>
<meta charset="UTF-8">
<title>Certificate of Completion</title>
<link href="https://fonts.googleapis.com/css2?family=Poppins:wght@400;500;600;800&family=Great+Vibes&display=swap" rel="stylesheet">
<style>
  :root {
    --navy: #1f2a78;
    --navy-dark: #141c55;
    --navy-light: #2c3a94;
    --gold: #f2c21b;
    --ink: #161616;
    --muted: #444;
    --paper: #ffffff;
    --paper-shade: #f1f2f5;
    --backdrop: #e6e7ee;
  }
  * { margin: 0; padding: 0; box-sizing: border-box; }
  html, body {
    width: 835px; height: 1200px; overflow: hidden;
    background: var(--backdrop);
    font-family: "Poppins", sans-serif;
  }
  .canvas {
    width: 835px; height: 1200px;
    display: flex; align-items: center; justify-content: center;
  }
  .certificate {
    position: relative;
    width: 775px; height: 570px;
    background:
      linear-gradient(128deg, transparent 0 38%, var(--paper-shade) 38% 52%, transparent 52%),
      linear-gradient(58deg, transparent 0 60%, var(--paper-shade) 60% 70%, transparent 70%),
      var(--paper);
    box-shadow: 0 10px 30px rgba(20, 28, 85, 0.18);
    overflow: hidden;
    color: var(--ink);
  }
  .top-rule {
    position: absolute; top: 52px; height: 5px; background: var(--navy);
  }
  .top-rule--left { left: 0; width: 300px; }
  .top-rule--right { right: 0; width: 300px; }
  .top-rule::after {
    content: ""; position: absolute; top: 0; width: 26px; height: 5px; background: var(--gold);
  }
  .top-rule--left::after { right: 0; }
  .top-rule--right::after { left: 0; }
  .brand {
    position: absolute; top: 34px; left: 50%; transform: translateX(-50%);
    display: flex; align-items: center; gap: 7px;
  }
  .brand-mark { width: 26px; height: 26px; background: var(--navy); }
  .brand-name {
    font-size: 9.5px; font-weight: 600; line-height: 1.15; color: var(--navy);
    text-transform: uppercase; width: 110px;
  }
  .title {
    position: absolute; top: 82px; width: 100%; text-align: center;
    font-size: 60px; font-weight: 800; letter-spacing: 1px; line-height: 1;
  }
  .ribbon { position: absolute; top: 152px; left: 50%; transform: translateX(-50%); }
  .presented {
    position: absolute; top: 206px; width: 100%; text-align: center;
    font-size: 16px; font-weight: 500; letter-spacing: 5px;
  }
  .recipient {
    position: absolute; top: 222px; width: 100%; text-align: center;
    font-family: "Great Vibes", cursive; font-size: 64px; line-height: 1.2;
  }
  .recipient-rule {
    position: absolute; top: 302px; left: 130px; right: 130px; height: 1px; background: var(--muted);
  }
  .statement {
    position: absolute; top: 316px; width: 100%; text-align: center;
    font-size: 17px; color: var(--ink);
  }
  .period {
    position: absolute; top: 352px; left: 130px; right: 130px;
    display: flex; gap: 28px; font-size: 16px;
  }
  .period-field { flex: 1; display: flex; align-items: flex-end; gap: 10px; }
  .period-line { flex: 1; height: 1px; background: var(--muted); margin-bottom: 6px; }
  .sign-field {
    position: absolute; top: 426px; width: 170px; text-align: center; font-size: 15px;
  }
  .sign-field::before {
    content: ""; display: block; height: 1px; background: var(--muted); margin-bottom: 6px;
  }
  .sign-field--signature { left: 120px; }
  .sign-field--date { right: 120px; }
  .footer-band { position: absolute; left: 0; bottom: 0; }
  .seal { position: absolute; left: 50%; top: 402px; transform: translateX(-50%); }
</style>
</head>
<body>
<main class="canvas">
  <article class="certificate">
    <div class="top-rule top-rule--left"></div>
    <div class="top-rule top-rule--right"></div>
    <div class="brand">
      <span class="brand-mark"></span>
      <span class="brand-name">Northfield Service Academy</span>
    </div>

    <h1 class="title">CERTIFICATE</h1>

    <svg class="ribbon" width="420" height="46" viewBox="0 0 420 46">
      <polygon points="0,10 50,10 50,44 0,44 14,27" fill="var(--navy-dark)"/>
      <polygon points="420,10 370,10 370,44 420,44 406,27" fill="var(--navy-dark)"/>
      <polygon points="40,38 50,44 50,38" fill="#0c1238"/>
      <polygon points="380,38 370,44 370,38" fill="#0c1238"/>
      <rect x="40" y="2" width="340" height="36" fill="var(--navy)"/>
      <text x="210" y="28" text-anchor="middle" fill="#fff" font-family="Poppins, sans-serif" font-weight="600" font-size="22" letter-spacing="2">OF COMPLETION</text>
    </svg>

    <p class="presented">PRESENTED TO</p>
    <p class="recipient">Daniel Carter</p>
    <div class="recipient-rule"></div>
    <p class="statement">For successfully completing our online training course</p>

    <div class="period">
      <div class="period-field"><span>From</span><span class="period-line"></span></div>
      <div class="period-field"><span>To</span><span class="period-line"></span></div>
    </div>

    <svg class="footer-band" width="775" height="105" viewBox="0 0 775 105">
      <polygon points="0,18 775,18 775,105 0,105" fill="var(--navy)"/>
      <polygon points="0,18 260,18 220,105 0,105" fill="var(--navy-light)"/>
      <polygon points="775,18 515,18 555,105 775,105" fill="var(--navy-light)"/>
      <rect x="0" y="10" width="180" height="3" fill="var(--gold)"/>
      <rect x="595" y="10" width="180" height="3" fill="var(--gold)"/>
    </svg>

    <div class="sign-field sign-field--signature">Signature</div>
    <div class="sign-field sign-field--date">Date</div>

    <svg class="seal" width="90" height="90" viewBox="0 0 90 90" role="img" aria-label="Award seal">
      <circle cx="45" cy="45" r="43" fill="#d9a91a"/>
      <circle cx="45" cy="45" r="35" fill="#fff"/>
      <circle cx="45" cy="45" r="22" fill="var(--navy)"/>
    </svg>
  </article>
</main>
</body>
</html>
```